Suchen ansprechendes & seriöses Urkunden/Zertifikat Design für Webseite & Druck
Zielgruppe
Auf unserer Webseite http://wacker-im-alter.de können sich Unternehmen, Institutionen und Vereine ihre Seniorenfreundlichkeit durch ein Zertifikat bestätigen und zertifizieren lassen.
Unsere Kundengruppen: Hotel – Gastronomie – Wellness – Reisen und Touristik – Touristikregionen – Seniorenshop – Onlineshop – Unternehmen als Dienstleister – Medizin und Health-Service – Apotheke – Altenheim – Pflegeheim – Seniorenheim – Vereine – Seniorenservice – Zahnärzte – Fitnessstudio – Sportstudio – Physiotherapie – Sportverein – Golfclub – und viele weitere seniorenfreundliche Institutionen.
Aufgabenstellung
Auftrag- Ausschreibung:
- Erstellung eines Design:
- Urkunde für Webseite wacker-im-alter.de - Das Zertifikat "Wacker im Alter“
Funktion:
Kunde erkennt das Zertifikat - Logo auf einer Webseite und Klickt auf dieses.
Er wird weitergeleitet auf eine Unterseite, worin die Richtlinien und die Urkunde sichtbar wird.
Zielgruppe:
- Unternehmen, welche das Zertifikat auf Ihre Webseite setzen. Die Urkunde gibt Auskunft, dass der Dienstleister einen besonderen Service für Senioren ausübt. Die Urkunde ist sichtbar auf der Webseite, indem das Logo angeklickt wird. Die Urkunde gibt es ebenfalls als Download, damit der Kunde diese in seinen Geschäftsräumen aufhängen kann oder diese in seinen Werbeunterlagen präsentieren kann.
- Verbraucher sollen beeindruckt sein, von der Urkunde, welches Vertrauen ausstrahlt, aber auch Seriosität
Folgende Ausstrahlung soll die Urkunde haben:
- Soll Mitbewerber des Zertifikatsinhaber beeindrucken und das Verlangen aufzeigen, sich ebenfalls zertifizieren zu lassen ( ca: 70% der Kunden sind Mitbewerber … ). Nach dem Motto "Das Logo ist super und edel, das muss ich auch haben!"
- Der Kunde als Verbraucher soll Vertrauen gewinnen, die Daten sollen gut sichtbar sein, aber nicht verkitscht wie eine Urkunde bei einer Kaffeefahrt. Der Verbraucher geht auf das Zertifikat und kommt zur Urkunde, deshalb soll die Farbe, und Darstellung, Seriosität des Unternehmens ausstrahlen.
Sonstiges
- Die Urkunde soll dem neuen Design unserer Seite (zu sehen unter: http://gutsiegel-pruefung.de) angepasst sein.
- Vor Auftragsendvergabe erhalten Sie noch ein telefonisches Briefing über unsere Erfahrungswerte
Link zur bestehenden alten Webseite (Altes Design): http://wacker-im-alter.de
Info Verbraucher: http://www.wacker-im-alter.de/verbraucher/
Info zum Zertifikat: http://www.wacker-im-al..

```html
<!DOCTYPE html>
<html lang="de">
<head>
<meta charset="utf-8">
<title>Zertifikat – Wacker im Alter</title>
<link rel="stylesheet" href="https://fonts.googleapis.com/css2?family=Raleway:wght@200;300;400;500&display=swap">
<style>
  :root {
    --paper: #ffffff;
    --gold: #b29a6c;
    --gold-dark: #8c6a3a;
    --ink: #3a3a3a;
    --seal: #e9e4da;
    --signature: #e6e2db;
  }
  * { margin: 0; padding: 0; box-sizing: border-box; }
  html, body { width: 850px; height: 1200px; overflow: hidden; background: var(--paper); }
  .certificate {
    position: relative; width: 850px; height: 1200px;
    font-family: "Raleway", sans-serif; color: var(--ink);
  }
  .frame { position: absolute; inset: 0; }
  .title {
    position: absolute; top: 100px; left: 0; width: 850px; text-align: center;
    font-weight: 200; font-size: 118px; letter-spacing: 4px; color: var(--gold);
    line-height: 1;
  }
  .subtitle {
    position: absolute; top: 222px; left: 0; width: 850px; text-align: center;
    font-weight: 300; font-size: 44px; letter-spacing: 1px; color: var(--ink);
  }
  .details { position: absolute; top: 325px; left: 0; width: 850px; }
  .row { display: flex; font-size: 23px; line-height: 30px; margin-bottom: 25px; }
  .label {
    width: 350px; text-align: right; padding-right: 10px;
    font-weight: 500; color: var(--gold-dark);
  }
  .value { font-weight: 400; color: var(--ink); }
  .row-tight { margin-bottom: 8px; }
  .confirm {
    position: absolute; top: 922px; width: 350px; padding-right: 10px; text-align: right;
    font-size: 23px; font-weight: 500; color: var(--gold-dark);
  }
  .signature {
    position: absolute; top: 975px; height: 62px; border-radius: 30px;
    background: var(--signature);
  }
  .signature-one { left: 150px; width: 150px; }
  .signature-two { left: 300px; width: 150px; }
  .signer { position: absolute; top: 1040px; font-size: 16px; color: var(--ink); }
  .signer-one { left: 165px; }
  .signer-two { left: 308px; }
  .seal {
    position: absolute; left: 465px; top: 892px; width: 210px; height: 210px;
    border-radius: 50%; background: var(--seal); border: 6px solid #d8d2c6;
  }
  .page-number {
    position: absolute; left: 22px; top: 1162px; font-size: 20px; font-weight: 500; color: var(--gold);
  }
</style>
</head>
<body>
<div class="certificate">
  <svg class="frame" width="850" height="1200" viewBox="0 0 850 1200" aria-hidden="true">
    <g fill="none" stroke="var(--gold)">
      <rect x="68" y="68" width="712" height="1064" stroke-width="1.5"/>
      <rect x="76" y="76" width="696" height="1048" stroke-width="1"/>
      <line x1="68" y1="320" x2="68" y2="880" stroke-width="3"/>
      <line x1="780" y1="320" x2="780" y2="880" stroke-width="3"/>
      <line x1="100" y1="1120" x2="750" y2="1120" stroke-width="4" stroke-dasharray="2 3"/>
      <line x1="100" y1="80" x2="750" y2="80" stroke-width="4" stroke-dasharray="2 3"/>
    </g>
  </svg>

  <h1 class="title">ZERTIFIKAT</h1>
  <h2 class="subtitle">WACKER IM ALTER</h2>

  <div class="details">
    <div class="row"><div class="label">Zertifikat ID:</div><div class="value">7250441e9e</div></div>
    <div class="row"><div class="label">Anbieter:</div><div class="value">Wacker im Alter<br>Ihr Zertifizierungsdienst</div></div>
    <div class="row"><div class="label">Status:</div><div class="value">aktiv</div></div>
    <div class="row"><div class="label">Unternehmen:</div><div class="value">Senioren Service Lindner<br>Ahornweg 8<br>54321 Talheim<br>Deutschland<br>info@lindner-service.org</div></div>
    <div class="row"><div class="label">Vertretungs-<br>berechtigter:</div><div class="value">Frau Ingrid<br>Lindner</div></div>
    <div class="row row-tight"><div class="label">Erstprüfung am:</div><div class="value">07.04.2017</div></div>
    <div class="row"><div class="label">gültig bis:</div><div class="value">07.04.2019</div></div>
  </div>

  <div class="confirm">Bestätigt von:</div>
  <div class="signature signature-one" role="img" aria-label="Handschriftliche Unterschrift K. Brandt"></div>
  <div class="signature signature-two" role="img" aria-label="Handschriftliche Unterschrift S. Vogel"></div>
  <div class="signer signer-one">K. Brandt</div>
  <div class="signer signer-two">S. Vogel</div>

  <div class="seal" role="img" aria-label="Zertifikatssiegel"></div>

  <div class="page-number">22</div>
</div>
</body>
</html>
```